Investment company needing business card

We are wanting a business card which looks sharp and easy on the eye. We are thinking of having a business card with the logo embossed on it, to really make it stand out. We will only have a small amount of information of the business card, person's name, position, email address and phone number

Contact Information for Business Card

Danielle Frost
Executive Assistant
+64 21 473 5162
danielf@harwickpartners.co.nz

Requirements
Must have
• Embossed logo
Should not have
• Not to be busy

```html
<!DOCTYPE html>
<html lang="en">
<head>
<meta charset="utf-8">
<title>Harwick Partners — Business Card</title>
<link href="https://fonts.googleapis.com/css2?family=Open+Sans:wght@400;600;700&display=swap" rel="stylesheet">
<style>
  :root {
    --page: #e9e7e4;
    --card-white: #ffffff;
    --brand-green: #22b573;
    --brand-grey: #656565;
    --ink-white: #ffffff;
    --ink-light: #d9d9d9;
    --shadow: rgba(0, 0, 0, 0.18);
  }
  * { box-sizing: border-box; margin: 0; padding: 0; }
  html, body {
    width: 1200px;
    height: 997px;
    overflow: hidden;
    background: var(--page);
    font-family: "Open Sans", Arial, sans-serif;
  }
  .sheet {
    position: relative;
    width: 1200px;
    height: 997px;
  }
  .card {
    position: absolute;
    left: 250px;
    width: 700px;
    height: 400px;
    overflow: hidden;
    box-shadow: 0 6px 18px var(--shadow);
  }
  .card--front { top: 70px; background: var(--card-white); }
  .card--back { top: 527px; background: var(--brand-grey); }

  /* Wordmark */
  .wordmark {
    position: absolute;
    display: flex;
    align-items: center;
    gap: 14px;
    font-weight: 700;
    letter-spacing: 0.06em;
    text-transform: uppercase;
    line-height: 1;
  }
  .wordmark__mark { display: block; }
  .card--front .wordmark {
    top: 74px;
    left: 190px;
    font-size: 34px;
    color: var(--brand-green);
  }
  .card--front .wordmark__mark { width: 44px; height: 44px; background: var(--brand-grey); }
  .card--back .wordmark {
    top: 160px;
    left: 0;
    width: 100%;
    justify-content: center;
    font-size: 40px;
    color: var(--ink-white);
  }
  .card--back .wordmark__mark { width: 52px; height: 52px; background: var(--ink-white); }

  /* Front: contact band */
  .contact-band {
    position: absolute;
    left: 270px;
    top: 150px;
    width: 430px;
    height: 150px;
    background: var(--brand-green);
  }
  .contact-list {
    position: absolute;
    left: 330px;
    top: 182px;
    list-style: none;
    color: var(--ink-white);
    font-size: 16px;
    line-height: 30px;
  }
  .contact-icons {
    position: absolute;
    left: 282px;
    top: 182px;
    width: 34px;
  }
  .contact-icons svg { display: block; margin-bottom: 10px; }

  .name-tag {
    position: absolute;
    left: 45px;
    top: 240px;
    width: 280px;
    height: 96px;
    background: var(--brand-grey);
    padding: 20px 24px;
  }
  .name-tag__name {
    color: var(--brand-green);
    font-size: 21px;
    font-weight: 600;
    letter-spacing: 0.04em;
    text-transform: uppercase;
  }
  .name-tag__role {
    color: var(--ink-white);
    font-size: 16px;
    margin-top: 2px;
  }

  /* Back: website line */
  .website {
    position: absolute;
    top: 318px;
    left: 0;
    width: 100%;
    display: flex;
    align-items: center;
    justify-content: center;
    gap: 16px;
    color: var(--ink-light);
    font-size: 16px;
    letter-spacing: 0.14em;
  }
  .website__rule { width: 70px; height: 1px; background: var(--ink-light); }
</style>
</head>
<body>
<main class="sheet">

  <section class="card card--front" aria-label="Business card, front">
    <div class="wordmark"><span class="wordmark__mark"></span><span>Harwick Partners</span></div>

    <div class="contact-band"></div>

    <div class="contact-icons" aria-hidden="true">
      <svg width="20" height="20" viewBox="0 0 20 20"><path d="M5 2l3 3-2 2c1 2 3 4 5 5l2-2 3 3-2 3C8 16 4 12 2 5z" fill="#fff"/></svg>
      <svg width="20" height="20" viewBox="0 0 20 20"><rect x="2" y="5" width="16" height="11" fill="none" stroke="#fff" stroke-width="1.6"/><path d="M2 5l8 6 8-6" fill="none" stroke="#fff" stroke-width="1.6"/></svg>
      <svg width="20" height="20" viewBox="0 0 20 20"><circle cx="10" cy="10" r="8" fill="none" stroke="#fff" stroke-width="1.6"/><ellipse cx="10" cy="10" rx="3.5" ry="8" fill="none" stroke="#fff" stroke-width="1.4"/><path d="M2 10h16" stroke="#fff" stroke-width="1.4"/></svg>
    </div>

    <ul class="contact-list">
      <li>+64 21 473 5162</li>
      <li>danielf@harwickpartners.co.nz</li>
      <li>www.harwickpartners.co.nz</li>
    </ul>

    <div class="name-tag">
      <p class="name-tag__name">Danielle Frost</p>
      <p class="name-tag__role">Executive Assistant</p>
    </div>
  </section>

  <section class="card card--back" aria-label="Business card, back">
    <div class="wordmark"><span class="wordmark__mark"></span><span>Harwick Partners</span></div>
    <p class="website"><span class="website__rule"></span>www.harwickpartners.co.nz<span class="website__rule"></span></p>
  </section>

</main>
</body>
</html>
```